Stationery Design Project

Hi All,

We need you to design stationary for a new Business and Accounting Advisory Firm. We have already got the logo designed and it is attached. If you could also if possible, match the fonts in your design to that on the logo’s provided.

What we need:
- Business Card
- A4 Letter head
- A4 Folders
- PPT template (Title page and regular page)

And what ever else you want to throw in.

We are in the process of getting the web site designed, however below is a list of websites which we like which will give you an understanding of the style that we are going for.

- plivant.example
- moldrabay.example
- tarvenhook.example
- quillorbank.example

I look forward to your seeing your design.
Updates

Hi All,

I have just realised that I forgot that i need to include a Sworn Ledgerkeepers image on the letter head, please find attaced as File 1. Could you please have this image in the bottom left header.

Regards,

Marcus

Industry/Entity Type

Business

Requirements
Must have
• Outputs:
- Documents ready to print
- Generic editable information
- Pdf copies of the documents
- Word version of letterhead

```html
<!DOCTYPE html>
<html lang="en">
<head>
<meta charset="utf-8">
<title>Brenmoor Partners – Business Cards</title>
<link rel="stylesheet" href="https://fonts.googleapis.com/css2?family=EB+Garamond:wght@500&family=Source+Sans+3:wght@400&display=swap">
<style>
  :root {
    --backdrop: #ececec;
    --card: #ffffff;
    --navy: #3a5796;
    --ink: #38499a;
    --band-top: #3fb7da;
    --band-bottom: #3a5a9b;
    --orange-top: #f28a1e;
    --orange-bottom: #f6a623;
    --white: #ffffff;
  }
  * { margin: 0; padding: 0; box-sizing: border-box; }
  html, body { width: 1200px; height: 1000px; overflow: hidden; }
  body {
    position: relative;
    background: var(--backdrop);
    font-family: "Source Sans 3", "Myriad Pro", Arial, sans-serif;
  }
  .card {
    position: absolute;
    background: var(--card);
    border: 1px solid #d2d2d2;
    overflow: hidden;
  }
  .card--front { left: 190px; top: 200px; width: 476px; height: 271px; }
  .card--back  { left: 517px; top: 501px; width: 471px; height: 268px; }

  .brand-block {
    position: absolute; left: 0; top: 19px; width: 24px; height: 65px;
    background: linear-gradient(90deg, var(--orange-top), var(--orange-bottom));
  }
  .brand-name {
    position: absolute; left: 40px; top: 24px;
    font-family: "EB Garamond", Garamond, serif;
    font-weight: 500; font-size: 33px; line-height: 1;
    color: var(--navy); white-space: nowrap;
  }
  .brand-tagline {
    position: absolute; left: 42px; top: 66px;
    font-size: 13px; letter-spacing: 8.8px;
    color: var(--navy); white-space: nowrap;
  }
  .name-band {
    position: absolute; left: 209px; right: 0; top: 101px; height: 82px;
    background: linear-gradient(180deg, var(--band-top), var(--band-bottom));
    color: var(--white);
  }
  .person-name { position: absolute; left: 27px; top: 8px; font-size: 27px; }
  .person-role { position: absolute; left: 137px; top: 46px; font-size: 19px; }
  .contact {
    position: absolute; left: 97px; top: 205px;
    font-size: 14.5px; line-height: 20.5px; color: var(--ink);
    white-space: nowrap;
  }
  .contact .fax { margin-left: 22px; }

  .back-name {
    position: absolute; left: 0; right: 0; top: 88px;
    text-align: center;
    font-family: "EB Garamond", Garamond, serif;
    font-weight: 500; font-size: 44px; color: var(--navy);
  }
  .back-mark {
    position: absolute; left: 225px; top: 160px; width: 22px; height: 22px;
    background: linear-gradient(180deg, var(--orange-top), var(--orange-bottom));
  }
  .website {
    position: absolute; left: 0; right: 0; top: 226px;
    text-align: center; font-size: 16.5px; color: var(--ink);
  }
</style>
</head>
<body>
  <section class="card card--front" aria-label="Business card front">
    <div class="brand-block"></div>
    <div class="brand-name">Brenmoor Partners</div>
    <div class="brand-tagline">Business Advisors</div>
    <div class="name-band">
      <div class="person-name">Evan Tallis</div>
      <div class="person-role">Partner</div>
    </div>
    <div class="contact">
      <p>4817 Harrow Ln. Linfield, Dorvale, 60231</p>
      <p>P: (555) 318-2046<span class="fax">F: (555) 318-2047</span></p>
      <p>E: evantallis@brenmoorpartners.example</p>
    </div>
  </section>

  <section class="card card--back" aria-label="Business card back">
    <div class="back-name">Brenmoor Partners</div>
    <div class="back-mark"></div>
    <div class="website">www.brenmoorpartners.example</div>
  </section>
</body>
</html>
```